Flat Belly Design Graphics for Social

I want to create 9 social media graphics (new Instagram size 4:5 (1080 x 1350 pixels) focusing on our Flat Belly Graphics, using the pics attached. Use the attached pics, NO RANDOM STOCK PHOTOGRAPHY. For the color scheme of the graphics, the color palette is attached. YOU MUST POST ALL 9 GRAPHICS IN ONE ENTRY.
Using the 3 titles below, create one set of graphics. 1) with all text, then for the others, use the pictures as detailed below in IMPORTANT:
1. Ten-Week Bright Morning Reboot
2. The Quick Garden Kitchen Menu Guide
3. Studio Habits for Lasting Energy Past Midlife - Zero Gym Needed
IMPORTANT:
Only use RK Pic 1 and RK Pic 2 with the title, Ten-Week Bright Morning Reboot
Only use meal plan1 and meal plan2 pics with the title, Quick Garden Kitchen Menu Guide
Only use studio habits 1 and studio habits 2 pics with the title, Studio Habits for Lasting Energy Past Midlife - Zero Gym Needed
women over 40

```html
<!DOCTYPE html>
<html lang="en">
<head>
<meta charset="utf-8">
<title>Set 1 – Ten-Week Bright Morning Reboot</title>
<link href="https://fonts.googleapis.com/css2?family=Anton&family=Permanent+Marker&display=block" rel="stylesheet">
<style>
  :root {
    --forest: #0b4d22;
    --forest-soft: #257f4e;
    --orchid: #ec8ad9;
    --blush: #f9d6ec;
    --paper: #ffffff;
    --outline: #1a1a1a;
  }
  * { box-sizing: border-box; margin: 0; padding: 0; }
  html, body { width: 1200px; height: 1000px; overflow: hidden; background: var(--paper); }
  .sheet { position: relative; width: 1200px; height: 1000px; font-family: "Anton", "Arial Narrow", sans-serif; }

  .swatch { position: absolute; left: 103px; width: 50px; height: 50px; }
  .swatch--forest { top: 71px; background: var(--forest); }
  .swatch--orchid { top: 133px; background: var(--orchid); }
  .swatch--blush { top: 195px; background: var(--blush); }

  .set-label, .set-title {
    position: absolute; left: 226px; color: var(--forest);
    font-weight: 400; line-height: 1; letter-spacing: -0.5px;
  }
  .set-label { top: 88px; font-size: 44px; }
  .set-title { top: 178px; font-size: 44px; }

  .post {
    position: absolute; top: 344px; width: 342px; height: 443px;
    border: 1px solid var(--outline);
  }
  .post--one { left: 54px; background: var(--forest); overflow: hidden; }
  .post--two { left: 425px; overflow: hidden; }
  .post--three { left: 795px; }

  .photo { position: absolute; }
  .post--one .photo {
    left: 0; top: 0; width: 290px; height: 443px;
    background: linear-gradient(180deg, #2a1f1c 0%, #a86d52 20%, #f1efe8 38%, #e9e6dd 60%, #8a5a40 70%, #16151a 80%);
    clip-path: polygon(40px 0, 120px 0, 135px 60px, 132px 135px, 200px 150px, 215px 230px, 228px 282px, 280px 266px, 286px 300px, 240px 332px, 212px 322px, 192px 342px, 192px 443px, 0 443px, 0 142px, 30px 130px, 24px 60px);
  }
  .post--two .photo {
    inset: 0;
    background: linear-gradient(180deg, #6c5a50 0%, #efece5 12%, #f3f1ea 55%, #8d5b3e 66%, #16151a 78%, #1d1a1c 100%);
  }
  .post--three .photo {
    inset: 0; overflow: hidden;
    background: linear-gradient(180deg, #5a4236 0%, #8a6a56 25%, #c8a080 45%, #e8e4dc 60%, #8c5a3e 80%, #1b181a 100%);
  }

  .brush {
    font-family: "Permanent Marker", "Anton", sans-serif;
    display: inline-block; transform: skewX(-10deg); line-height: 1;
  }

  .title-card {
    position: absolute; background: var(--blush); color: var(--forest);
    clip-path: polygon(0 0, 100% 20%, 80% 100%, 6% 92%);
    display: flex; align-items: center; justify-content: center; white-space: nowrap;
    padding-right: 14px;
  }
  .title-card .unit { line-height: 1; margin-top: 8px; }
  .post--one .title-card { left: 134px; top: 11px; width: 197px; height: 122px; }
  .post--one .brush, .post--two .title-card .brush { font-size: 52px; }
  .post--one .unit, .post--two .unit { font-size: 28px; }
  .post--two .title-card { left: 50px; top: 30px; width: 196px; height: 123px; }
  .post--three .title-card { left: 23px; top: 25px; width: 148px; height: 88px; }
  .post--three .title-card .brush { font-size: 38px; }
  .post--three .unit { font-size: 21px; }

  .subtitle {
    position: absolute; color: var(--orchid); font-size: 28px; line-height: 1.05;
    transform: rotate(-3deg); text-align: center;
  }
  .post--one .subtitle { left: 192px; top: 128px; width: 126px; }
  .post--two .subtitle { left: 100px; top: 152px; width: 126px; }
  .subtitle-band {
    position: absolute; left: 16px; top: 113px; width: 146px; height: 73px;
    background: var(--forest); color: var(--orchid);
    clip-path: polygon(0 2%, 100% 0, 98% 98%, 3% 100%);
    display: flex; flex-direction: column; align-items: center; justify-content: center;
    font-size: 24px; line-height: 1.05;
  }

  .closing-box {
    position: absolute; background: var(--blush); color: var(--forest);
    clip-path: polygon(0 0, 100% 0, 94% 100%, 6% 96%);
    display: flex; align-items: center; justify-content: center;
  }
  .closing-box .brush { font-size: 24px; }
  .post--one .closing-box { left: 212px; top: 200px; width: 108px; height: 70px; }
  .post--two .closing-box { left: 116px; top: 224px; width: 108px; height: 70px; }
  .post--three .closing-box { left: 47px; top: 190px; width: 104px; height: 70px; }

  .decor { position: absolute; overflow: visible; }
  .waist-line { fill: none; stroke: var(--orchid); stroke-width: 3; }
</style>
</head>
<body>
<main class="sheet">
  <div class="swatch swatch--forest"></div>
  <div class="swatch swatch--orchid"></div>
  <div class="swatch swatch--blush"></div>
  <h1 class="set-label">Set 1</h1>
  <h2 class="set-title">Ten-Week Bright Morning Reboot</h2>

  <section class="post post--one">
    <div class="photo" role="img" aria-label="Cut-out of a smiling woman in a white cropped sweater and dark jeans, pointing toward the title"></div>
    <svg class="decor" style="left:170px;top:260px" width="175" height="190" viewBox="0 0 175 190">
      <polygon fill="var(--forest-soft)" transform="translate(0,80)" points="50,0 61,35 98,35 68,57 79,91 50,70 21,91 32,57 2,35 39,35"/>
      <polygon fill="var(--forest-soft)" transform="translate(95,110) scale(0.78)" points="50,0 61,35 98,35 68,57 79,91 50,70 21,91 32,57 2,35 39,35"/>
      <polygon fill="var(--orchid)" transform="translate(95,80) scale(0.2)" points="50,0 61,35 98,35 68,57 79,91 50,70 21,91 32,57 2,35 39,35"/>
      <polygon fill="var(--orchid)" transform="translate(117,47) scale(0.11)" points="50,0 61,35 98,35 68,57 79,91 50,70 21,91 32,57 2,35 39,35"/>
      <polygon fill="var(--orchid)" transform="translate(133,15) scale(0.07)" points="50,0 61,35 98,35 68,57 79,91 50,70 21,91 32,57 2,35 39,35"/>
    </svg>
    <div class="title-card"><span class="brush">Ten</span><span class="unit">-Week</span></div>
    <p class="subtitle">Bright<br>Morning</p>
    <div class="closing-box"><span class="brush">Reboot</span></div>
  </section>

  <section class="post post--two">
    <div class="photo" role="img" aria-label="Close crop of a woman's midriff in a white cropped sweater, hands pressing in at the waist"></div>
    <svg class="decor" style="left:0;top:0" width="342" height="443" viewBox="0 0 342 443">
      <path class="waist-line" d="M0 96 C 55 180, 70 330, 0 432"/>
      <path class="waist-line" d="M342 66 C 280 160, 270 330, 342 428"/>
      <path class="waist-line" d="M8 214 L 52 242 M46 236 l 6 6 -8 2"/>
      <path class="waist-line" d="M4 268 L 52 270 M46 266 l 6 4 -6 4"/>
      <path class="waist-line" d="M334 222 L 290 246 M296 240 l -6 6 8 2"/>
      <path class="waist-line" d="M336 320 L 292 306 M298 302 l -6 4 6 5"/>
    </svg>
    <div class="title-card"><span class="brush">Ten</span><span class="unit">-Week</span></div>
    <p class="subtitle">Bright<br>Morning</p>
    <div class="closing-box"><span class="brush">Reboot</span></div>
  </section>

  <section class="post post--three">
    <div class="photo" role="img" aria-label="Smiling woman in a white cropped sweater standing in a kitchen, pointing to her waist"></div>
    <svg class="decor" style="left:0;top:280px" width="180" height="190" viewBox="0 0 180 190">
      <polygon fill="var(--blush)" fill-opacity="0.45" transform="translate(0,90)" points="50,0 61,35 98,35 68,57 79,91 50,70 21,91 32,57 2,35 39,35"/>
      <polygon fill="var(--blush)" fill-opacity="0.55" transform="translate(95,110) scale(0.7)" points="50,0 61,35 98,35 68,57 79,91 50,70 21,91 32,57 2,35 39,35"/>
      <polygon fill="var(--orchid)" transform="translate(48,72) scale(0.2)" points="50,0 61,35 98,35 68,57 79,91 50,70 21,91 32,57 2,35 39,35"/>
      <polygon fill="var(--orchid)" transform="translate(28,38) scale(0.11)" points="50,0 61,35 98,35 68,57 79,91 50,70 21,91 32,57 2,35 39,35"/>
      <polygon fill="var(--orchid)" transform="translate(22,8) scale(0.07)" points="50,0 61,35 98,35 68,57 79,91 50,70 21,91 32,57 2,35 39,35"/>
    </svg>
    <div class="title-card"><span class="brush">Ten</span><span class="unit">-Week</span></div>
    <div class="subtitle-band"><span>Bright</span><span>Morning</span></div>
    <div class="closing-box"><span class="brush">Reboot</span></div>
  </section>
</main>
</body>
</html>
```